Autora necesita un cover para su nuevo libro acerca de empoderamiento femenino*

Diseño de cover para libro digital sobre empoderamiento femenino.

El título del libro es: "Las 7 Raíces del Alma Serena"
Subtítulo: Vive con raíz firme, calma y propósito

Autora: Rosalba Quintero

Target Market(s)

Mujeres

Font styles to use
Sans Serif

Requirements
Must have
• El título del libro es: "Las 7 Raíces del Alma Serena"

Autora: Rosalba Quintero
Should not have
• Sin imágenes

```html
<!DOCTYPE html>
<html lang="es">
<head>
<meta charset="UTF-8">
<title>Las 7 Raíces del Alma Serena — Rosalba Quintero</title>
<link rel="stylesheet" href="https://fonts.googleapis.com/css2?family=Oswald:wght@500;600&family=Kaushan+Script&family=Mr+Dafoe&family=Caveat:wght@500&display=swap">
<style>
  :root {
    --backdrop: #ebebeb;
    --paper: #ffffff;
    --ink-dark: #2b2d31;
    --band-dark: #26282c;
    --band-mid: #34363b;
    --gold-light: #f3d27a;
    --gold-mid: #d4a73c;
    --gold-deep: #a87a1e;
    --pink: #f0197a;
    --white: #ffffff;
  }
  * { margin: 0; padding: 0; box-sizing: border-box; }
  html, body {
    width: 1200px;
    height: 1200px;
    overflow: hidden;
    background: var(--backdrop);
  }
  .book-cover {
    position: absolute;
    left: 255px;
    top: 45px;
    width: 690px;
    height: 1110px;
    background: var(--paper);
    box-shadow: 0 6px 24px rgba(0,0,0,0.12);
    overflow: hidden;
  }
  .title {
    position: absolute;
    left: 0;
    top: 58px;
    width: 100%;
    text-align: center;
    font-weight: normal;
  }
  .title-row {
    display: block;
    white-space: nowrap;
  }
  .title-article {
    display: inline-block;
    font-family: "Mr Dafoe", cursive;
    font-size: 84px;
    line-height: 1;
    color: var(--ink-dark);
    text-transform: none;
    margin-right: 14px;
    vertical-align: 4px;
  }
  .title-line {
    display: inline-block;
    font-family: "Oswald", sans-serif;
    font-weight: 600;
    font-size: 118px;
    line-height: 1;
    letter-spacing: 1px;
    text-transform: uppercase;
    background: linear-gradient(180deg, var(--gold-light) 0%, var(--gold-mid) 55%, var(--gold-deep) 100%);
    -webkit-background-clip: text;
    background-clip: text;
    color: transparent;
  }
  .title-accent {
    display: block;
    margin-top: 20px;
    font-family: "Kaushan Script", cursive;
    font-size: 120px;
    line-height: 1;
    color: var(--pink);
  }
  .pillars-art {
    position: absolute;
    left: 92px;
    top: 446px;
    width: 518px;
    height: 347px;
    background: linear-gradient(90deg, var(--gold-deep) 0%, var(--gold-light) 30%, var(--gold-mid) 55%, var(--gold-light) 75%, var(--gold-deep) 100%);
  }
  .cover-band {
    position: absolute;
    left: 0;
    top: 793px;
    width: 100%;
    height: 317px;
    background: radial-gradient(ellipse at 50% 0%, var(--band-mid) 0%, var(--band-dark) 70%);
  }
  .subtitle {
    position: absolute;
    left: 0;
    top: 32px;
    width: 100%;
    text-align: center;
    font-family: "Caveat", cursive;
    font-weight: 500;
    font-size: 66px;
    line-height: 1.02;
    color: var(--white);
  }
  .author {
    position: absolute;
    left: 0;
    top: 196px;
    width: 100%;
    text-align: center;
    font-family: "Oswald", sans-serif;
    font-weight: 500;
    font-size: 46px;
    letter-spacing: 9px;
    text-transform: uppercase;
    background: linear-gradient(180deg, var(--gold-light) 0%, var(--gold-mid) 60%, var(--gold-deep) 100%);
    -webkit-background-clip: text;
    background-clip: text;
    color: transparent;
  }
</style>
</head>
<body>
  <main class="book-cover">
    <h1 class="title">
      <span class="title-row"><span class="title-article">Las</span><span class="title-line">7 Raíces</span></span>
      <span class="title-row"><span class="title-line">Del Alma</span></span>
      <span class="title-accent">Serena</span>
    </h1>
    <div class="pillars-art" role="img" aria-label="Ilustración de cinco columnas clásicas doradas"></div>
    <section class="cover-band">
      <p class="subtitle">Vive con raíz firme,<br>calma y propósito</p>
      <p class="author">Rosalba Quintero</p>
    </section>
  </main>
</body>
</html>
```